Values and Organizational Purpose Signage

We recently solidified our company values, organizatioanal purpose and strategic vision. I'd like to develop some tasteful (not overly corporate) signage of these values to display in our office.

I've attached the hand-written values and purpose that my core team members then initialed acknowleding they align along with the signage at the front of our office to provide some perspective on our brand identity.

Industry/Entity Type

It Company

Font styles to use
Sans Serif

Requirements
Must have
• I'd like to see the values and org purpose depicted as one sign and as separate signs (i.e., values on one sign and org purpose on another). I need it to reflect our brand identity which I've uploaded

```html
<!DOCTYPE html>
<html lang="en">
<head>
<meta charset="utf-8">
<title>Organizational Purpose and Core Values Signage</title>
<link rel="stylesheet" href="https://fonts.googleapis.com/css2?family=Jost:wght@400;500;700;800&display=swap">
<style>
  :root {
    --backdrop: #e9ece6;
    --sign-face: #ffffff;
    --ink: #0d3a3a;
    --rule: #7c9c2b;
    --mount: #123434;
  }
  * { margin: 0; padding: 0; box-sizing: border-box; }
  html, body {
    width: 1200px;
    height: 748px;
    overflow: hidden;
    background: var(--backdrop);
    font-family: "Jost", sans-serif;
    color: var(--ink);
  }
  .canvas { position: relative; width: 1200px; height: 748px; }

  .sign {
    position: absolute;
    left: 334px;
    width: 531px;
    background: var(--sign-face);
    box-shadow: 0 3px 10px rgba(0, 0, 0, 0.18);
    overflow: hidden;
  }
  .sign--purpose { top: 64px; height: 181px; }
  .sign--values { top: 320px; height: 363px; }

  .mount {
    position: absolute;
    width: 8px; height: 8px;
    border-radius: 50%;
    background: var(--mount);
  }
  .mount--tl { left: 4px; top: 6px; }
  .mount--tr { right: 5px; top: 6px; }
  .mount--bl { left: 4px; bottom: 6px; }
  .mount--br { right: 5px; bottom: 6px; }

  .sign__title {
    position: absolute;
    font-weight: 800;
    line-height: 1;
    white-space: nowrap;
  }
  .sign--purpose .sign__title { left: 40px; top: 36px; font-size: 29px; letter-spacing: 0.2px; }
  .sign--values .sign__title { left: 26px; top: 34px; font-size: 37.5px; letter-spacing: 0.2px; }

  .rule {
    position: absolute;
    left: 41px;
    width: 445px;
    height: 6px;
    background: var(--rule);
  }

  .purpose-statement {
    position: absolute;
    left: 45px;
    top: 94px;
    font-size: 26px;
    font-weight: 400;
    line-height: 30px;
    white-space: nowrap;
  }

  .value__name {
    position: absolute;
    left: 41px;
    font-size: 19px;
    font-weight: 700;
    letter-spacing: 0.3px;
    line-height: 22px;
    transform: translateY(-50%);
  }
  .value__desc {
    position: absolute;
    left: 228px;
    width: 262px;
    font-size: 14.5px;
    font-weight: 400;
    line-height: 18px;
  }
</style>
</head>
<body>
<main class="canvas">

  <section class="sign sign--purpose" aria-label="Organizational purpose sign">
    <span class="mount mount--tl"></span><span class="mount mount--tr"></span>
    <span class="mount mount--bl"></span><span class="mount mount--br"></span>
    <h2 class="sign__title">ORGANIZATIONAL PURPOSE</h2>
    <div class="rule" style="top:76px"></div>
    <p class="purpose-statement">We deliver simple and digestible<br>solutions to complex matters</p>
  </section>

  <section class="sign sign--values" aria-label="Core values sign">
    <span class="mount mount--tl"></span><span class="mount mount--tr"></span>
    <span class="mount mount--bl"></span><span class="mount mount--br"></span>
    <h2 class="sign__title">CORE VALUES DEFINED</h2>

    <h3 class="value__name" style="top:107px">RESPECT</h3>
    <p class="value__desc" style="top:86px">We are transparent and receptive to the thoughts, opinion and feelings of others</p>
    <div class="rule" style="top:127px"></div>

    <h3 class="value__name" style="top:167px">INTEGRITY</h3>
    <p class="value__desc" style="top:155px">We uphold our promises</p>
    <div class="rule" style="top:189px"></div>

    <h3 class="value__name" style="top:229px">EXCELLENCE</h3>
    <p class="value__desc" style="top:206px">We continuously strive to be the best in<br>all endeavors</p>
    <div class="rule" style="top:249px"></div>

    <h3 class="value__name" style="top:293px">OPEN<br>MINDEDNESS</h3>
    <p class="value__desc" style="top:272px">We encourage creative and innovative expressions</p>
  </section>

</main>
</body>
</html>
```